Web Developer Needs a Business Card Design

I need a personal business card design that represents me as a web developer for potential employers. I would like the background to be a dark color on the front for contrast with my logo and name. The back will have all my information along with a smaller version of the logo. I want something with a modern look and feel, not too conservative. This will be used for potential employers and freelance work.

Industry/Entity Type

Business

Contact Information for Business Card

Front should have my logo and name. The back should have all my personal information which would include: name: Tom Varulek, phone: 570-614-3098, email: tomvarulek@quillbox.net, website url: www.tomvarulek.net, logo, web developer.

Font styles to use
Sans Serif

Requirements
Must have
• Must include my logo. The color palette base color will be the logo color.

```html
<!DOCTYPE html>
<html lang="en">
<head>
<meta charset="utf-8">
<title>Tom Varulek – Business Card</title>
<link href="https://fonts.googleapis.com/css2?family=Arimo:wght@400;700&display=swap" rel="stylesheet">
<style>
  :root {
    --backdrop: #e9e6e1;
    --card-white: #ffffff;
    --teal: #5fbfaa;
    --ink: #0b0b0b;
    --light-text: #f2f2f2;
  }
  html, body {
    margin: 0;
    padding: 0;
    width: 1200px;
    height: 902px;
    overflow: hidden;
    background: var(--backdrop);
  }
  .card {
    position: absolute;
    left: 110px;
    top: 171px;
    width: 980px;
    height: 560px;
    background: var(--card-white);
    box-shadow: 0 10px 30px rgba(0,0,0,0.18);
    overflow: hidden;
    font-family: "Arimo", Arial, sans-serif;
  }
  .card-art {
    position: absolute;
    inset: 0;
  }
  .brand-name {
    font-family: "Arimo", Arial, sans-serif;
    font-weight: 700;
    font-size: 27px;
    fill: var(--teal);
  }
  .identity {
    position: absolute;
    left: 48px;
    bottom: 34px;
    color: var(--light-text);
  }
  .identity-name {
    margin: 0;
    font-size: 50px;
    font-weight: 700;
    line-height: 1.05;
  }
  .identity-role {
    margin: 4px 0 0 4px;
    font-size: 30px;
    font-weight: 700;
    line-height: 1.1;
  }
  .contact-list {
    position: absolute;
    left: 610px;
    top: 350px;
    margin: 0;
    padding: 6px 0 6px 24px;
    list-style: none;
    border-left: 2px solid var(--light-text);
    color: var(--light-text);
  }
  .contact-item {
    display: flex;
    align-items: center;
    gap: 16px;
    height: 50px;
    font-size: 24px;
  }
  .contact-icon {
    width: 26px;
    height: 26px;
    flex: none;
  }
</style>
</head>
<body>
  <div class="card">
    <svg class="card-art" viewBox="0 0 980 560" width="980" height="560">
      <path class="wave-accent" fill="var(--teal)"
        d="M0,330 C200,400 450,385 610,305 C730,245 850,232 980,226 L980,560 L0,560 Z"/>
      <path class="wave-base" fill="var(--ink)"
        d="M0,360 C200,430 450,415 615,335 C735,275 855,262 980,256 L980,560 L0,560 Z"/>
      <g class="brand-mark">
        <circle cx="470" cy="165" r="118" fill="none" stroke="var(--teal)" stroke-width="9"/>
        <text class="brand-name" x="470" y="174" text-anchor="middle">Tom Varulek</text>
      </g>
    </svg>

    <div class="identity">
      <p class="identity-name">Tom Varulek</p>
      <p class="identity-role">Web Developer</p>
    </div>

    <ul class="contact-list">
      <li class="contact-item">
        <svg class="contact-icon" viewBox="0 0 26 26" aria-hidden="true">
          <rect x="1" y="1" width="24" height="24" rx="3" fill="var(--light-text)"/>
          <path d="M8 6 C6 7 6 10 9 14 C12 18 15 20 17 19 L18.5 17.5 L16 15 L14.5 16 C13 15 11 13 10 11.5 L11 10 L8.5 6.5 Z" fill="var(--ink)"/>
        </svg>
        <span>570-614-3098</span>
      </li>
      <li class="contact-item">
        <svg class="contact-icon" viewBox="0 0 26 26" aria-hidden="true">
          <rect x="1" y="1" width="24" height="24" rx="3" fill="var(--light-text)"/>
          <rect x="5" y="8" width="16" height="11" fill="none" stroke="var(--ink)" stroke-width="1.8"/>
          <path d="M5 8 L13 14.5 L21 8" fill="none" stroke="var(--ink)" stroke-width="1.8"/>
        </svg>
        <span>tomvarulek@quillbox.net</span>
      </li>
      <li class="contact-item">
        <svg class="contact-icon" viewBox="0 0 26 26" aria-hidden="true">
          <rect x="1" y="1" width="24" height="24" rx="3" fill="var(--light-text)"/>
          <circle cx="13" cy="13" r="7.5" fill="none" stroke="var(--ink)" stroke-width="1.8"/>
          <ellipse cx="13" cy="13" rx="3.2" ry="7.5" fill="none" stroke="var(--ink)" stroke-width="1.4"/>
          <path d="M5.5 13 H20.5" stroke="var(--ink)" stroke-width="1.4"/>
        </svg>
        <span>www.tomvarulek.net</span>
      </li>
    </ul>
  </div>
</body>
</html>
```